Business Card Design Project

Business Card
We are rebranding with a new logo
Industry/Entity Type
Business
Contact Information for Business Card
Dennis Morvale +61 487215963 dennis@quorv.com.au P.O. Box 872 Fernlow QLD 4309
Requirements
Must have
- Logo

```html
<!DOCTYPE html>
<html lang="en">
<head>
<meta charset="utf-8">
<title>Quorv International – Business Card</title>
<link rel="stylesheet" href="https://fonts.googleapis.com/css2?family=Roboto:wght@400;700&family=Dancing+Script:wght@600&display=swap">
<style>
  :root {
    --page-bg: #e4e4e4;
    --card-bg: #fbfbfb;
    --brand-navy: #123f5a;
    --blue-light: #1f9bd7;
    --blue-deep: #0b4a6c;
    --orange: #ec7a1c;
    --ink: #1f2428;
    --white: #ffffff;
  }
  * { box-sizing: border-box; margin: 0; padding: 0; }
  html, body {
    width: 1200px; height: 576px; overflow: hidden;
    background: var(--page-bg);
  }
  .canvas { position: relative; width: 1200px; height: 576px; }
  .card {
    position: absolute; top: 138px;
    width: 484px; height: 294px;
    background: var(--card-bg);
    border-radius: 12px;
    overflow: hidden;
    box-shadow: 0 2px 5px rgba(0,0,0,0.18);
  }
  .card--front { left: 82px; }
  .card--back { left: 602px; }

  .brand {
    position: absolute;
    font-family: "Roboto", sans-serif;
    font-weight: 700;
    color: var(--brand-navy);
    text-align: center;
    line-height: 1;
  }
  .brand__name { display: block; font-size: 58px; letter-spacing: 2px; }
  .brand__sub { display: block; font-size: 16px; letter-spacing: 3.4px; margin-top: 12px; }
  .card--front .brand { left: 0; right: 0; top: 96px; }
  .card--back .brand { left: 48px; top: 80px; }
  .card--back .brand__name { font-size: 54px; }
  .card--back .brand__sub { font-size: 15px; letter-spacing: 3.2px; }

  .holder { position: absolute; right: 22px; top: 42px; text-align: right; }
  .holder__name {
    font-family: "Dancing Script", cursive;
    font-weight: 600; font-size: 27px;
    color: var(--brand-navy); line-height: 1;
  }
  .holder__role {
    font-family: "Roboto", sans-serif;
    font-size: 11px; color: var(--ink); margin-top: 5px;
  }

  .accent-band {
    position: absolute; left: 0; right: 0; bottom: 0; height: 94px;
    background: linear-gradient(90deg, var(--blue-light) 0%, #136d9a 55%, var(--blue-deep) 100%);
    border-top: 6px solid var(--orange);
  }

  .contact {
    position: absolute; right: 22px; top: 222px;
    list-style: none;
    font-family: "Roboto", sans-serif;
    font-size: 12px; color: var(--white);
  }
  .contact__item {
    display: flex; justify-content: flex-end; align-items: center;
    gap: 8px; height: 17px;
  }
  .contact__icon { width: 11px; height: 11px; fill: var(--orange); flex: none; }
</style>
</head>
<body>
<main class="canvas">

  <section class="card card--front" aria-label="Card front">
    <div class="brand">
      <span class="brand__name">QUORV</span>
      <span class="brand__sub">INTERNATIONAL</span>
    </div>
  </section>

  <section class="card card--back" aria-label="Card back">
    <div class="accent-band" role="img" aria-label="Decorative blue and orange wave band"></div>

    <div class="brand">
      <span class="brand__name">QUORV</span>
      <span class="brand__sub">INTERNATIONAL</span>
    </div>

    <div class="holder">
      <p class="holder__name">Dennis Morvale</p>
      <p class="holder__role">Managing Director</p>
    </div>

    <ul class="contact">
      <li class="contact__item">+61 487215963
        <svg class="contact__icon" viewBox="0 0 12 12" aria-hidden="true"><path d="M1,4 Q1,2 6,2 Q11,2 11,4 L11,5 L8.5,5 L8.5,4 L3.5,4 L3.5,5 L1,5 Z M2.5,6 L9.5,6 L10.5,10.5 L1.5,10.5 Z"/></svg>
      </li>
      <li class="contact__item">dennis@quorv.com.au
        <svg class="contact__icon" viewBox="0 0 12 12" aria-hidden="true"><path d="M1,2.5 L11,2.5 L11,9.5 L1,9.5 Z M1.6,3.2 L6,6.6 L10.4,3.2" stroke="var(--blue-deep)" stroke-width="0.8"/></svg>
      </li>
      <li class="contact__item">P.O. Box 872 Fernlow QLD 4309
        <svg class="contact__icon" viewBox="0 0 12 12" aria-hidden="true"><path d="M6,0.5 C8.6,0.5 10,2.3 10,4.4 C10,7 6,11.5 6,11.5 C6,11.5 2,7 2,4.4 C2,2.3 3.4,0.5 6,0.5 Z M6,3 A1.5,1.5 0 1 0 6,6 A1.5,1.5 0 1 0 6,3 Z" fill-rule="evenodd"/></svg>
      </li>
    </ul>
  </section>

</main>
</body>
</html>
```